Simple one page Wordpress website

We need a quick turnaround single page wordpress website.
The design needs to be very simple and clean.
We already have some design assets (logos and colours etc) and some draft copy for the page.

We need all the files for us to be able to create a wordpress site. We can do this ourselves and we will host it.

```html
<!DOCTYPE html>
<html lang="en">
<head>
<meta charset="utf-8">
<title>Vetrixo</title>
<link href="https://fonts.googleapis.com/css2?family=Roboto:wght@500;700&family=Lato:wght@400;700&display=swap" rel="stylesheet">
<style>
:root{
  --navy:#2e2d4d;
  --blue:#4f87b8;
  --green:#8fb31d;
  --ink:#222;
  --muted:#444;
  --white:#fff;
  --black:#000;
  --grad:linear-gradient(90deg,#4f87b8,#8fb31d);
}
*{box-sizing:border-box;margin:0;padding:0}
html,body{width:1200px;height:3789px;overflow:hidden}
body{position:relative;font-family:"Lato",sans-serif;color:var(--ink);background:var(--white)}
.abs{position:absolute}
h1,h2,h3,h4{font-family:"Roboto",sans-serif;font-weight:700}
.btn{position:absolute;display:flex;align-items:center;justify-content:center;font-family:"Roboto",sans-serif;font-weight:700;font-size:16px;color:var(--white);background:var(--grad);border-radius:4px;text-transform:uppercase}
.btn-outline{background:none;border:2px solid var(--white)}
.section-title{position:absolute;left:0;width:1200px;text-align:center;font-size:31px;color:var(--ink);text-transform:uppercase}
.title-bar{position:absolute;width:44px;height:5px;border-radius:3px;background:var(--navy)}
.tick{width:20px;height:20px;flex:none}

/* header */
.site-header{left:112px;top:32px;width:976px;height:77px;background:var(--white);border-radius:4px;box-shadow:0 2px 10px rgba(0,0,0,.1)}
.brand{position:absolute;left:24px;top:20px;font-family:"Roboto",sans-serif;font-weight:700;font-size:32px;letter-spacing:1px;color:var(--blue)}
.nav{position:absolute;left:230px;top:30px;display:flex;gap:44px;font-family:"Roboto",sans-serif;font-weight:500;font-size:15px;color:var(--ink)}
.nav .active{color:var(--blue)}
.nav .active::after{content:"";display:block;width:40px;height:3px;margin:6px auto 0;background:var(--navy);border-radius:2px}
.search{position:absolute;left:785px;top:28px}
.login{left:838px;top:15px;width:116px;height:47px;border-radius:6px}

/* hero */
.hero-photo{left:0;top:0;width:1200px;height:685px;background:linear-gradient(100deg,#b9a58f 0%,#c88c5c 30%,#8f9aa3 55%,#c9c6c0 80%,#a9a9a3 100%)}
.hero-blob{left:636px;top:155px;width:450px;height:450px}
.hero-copy{left:636px;top:0;width:450px;text-align:center;color:var(--white)}
.hero-kicker{position:absolute;left:0;width:450px;top:296px;font-family:"Roboto",sans-serif;font-weight:500;font-size:30px}
.hero-name{position:absolute;left:0;width:450px;top:345px;font-size:74px;line-height:1;letter-spacing:1px}
.hero-sub{position:absolute;left:0;width:450px;top:442px;font-size:15px}
.hero-btn{left:788px;top:493px;width:150px;height:47px}
.dots{left:578px;top:630px;display:flex;gap:6px;align-items:center}
.dots span{width:10px;height:10px;border-radius:50%;background:var(--white)}
.dots .on{width:14px;height:14px;border:3px solid var(--green)}

/* mission */
.mission{left:0;top:685px;width:1200px;height:411px;background:linear-gradient(180deg,#ececec,#f4f4f4)}
.mission-text{left:240px;top:838px;width:720px;text-align:center;font-size:19px;line-height:34px;color:#333}
.mission-btn{left:525px;top:977px;width:151px;height:48px}

/* capabilities */
.cap-title{left:112px;top:1178px;font-size:31px}
.cap-list{left:112px;top:1262px;width:478px;list-style:none;font-size:15px;line-height:26px;color:var(--muted)}
.cap-list li{display:flex;gap:20px;margin-bottom:18px}
.cap-list .tick{margin-top:6px}
.cap-btn{left:112px;top:1459px;width:151px;height:47px}
.cap-frame{left:621px;top:1172px;width:463px;height:355px;border-radius:46px 0 46px 0;background:var(--green)}
.cap-photo{left:621px;top:1180px;width:455px;height:347px;border-radius:40px 0 40px 0;background:linear-gradient(120deg,#c79a7a,#8b6a52 50%,#e2d9cf)}

/* turnkey */
.turnkey{left:0;top:1613px;width:1200px;height:561px;background:var(--navy)}
.turnkey-photo{left:0;top:1613px;width:640px;height:561px;background:linear-gradient(90deg,#d7c19c 0%,#cfc7bb 50%,rgba(46,45,77,0) 100%)}
.turnkey-copy{left:600px;top:1688px;width:500px;color:var(--white)}
.turnkey-copy h2{font-size:22px;line-height:38px;text-transform:uppercase}
.turnkey-copy p{margin-top:12px;font-size:14.5px;line-height:25.5px}
.turnkey-copy ul{list-style:none;margin-top:14px;font-size:15px}
.turnkey-copy li{display:flex;align-items:center;gap:18px;height:34.6px}
.turnkey-btn{left:600px;top:2057px;width:153px;height:50px}

/* joint venture */
.jv-card{top:2356px;width:472px;height:387px;border-radius:4px;color:var(--white);text-align:center}
.jv-card h3{position:absolute;left:0;width:100%;top:50px;font-size:26px;font-weight:500}
.jv-card p{position:absolute;left:36px;right:36px;top:106px;font-size:15px;line-height:26px}
.jv-blue{left:112px;background:linear-gradient(160deg,#5b8fc0,#4a80b2)}
.jv-green{left:616px;background:linear-gradient(160deg,#99bc2b,#85aa18)}
.jv-btn{left:158px;top:287px;width:155px;height:50px}

/* team */
.team{left:0;top:2829px;width:1200px;height:612px;background:linear-gradient(180deg,#f0f0f0,#f6f6f6)}
.member{top:3010px;width:260px;text-align:center}
.avatar-ring{position:absolute;left:27px;top:2px;width:206px;height:206px;border-radius:50%;background:var(--white);box-shadow:0 2px 10px rgba(0,0,0,.18)}
.avatar{position:absolute;left:37px;top:12px;width:186px;height:186px;border-radius:50%}
.member h4{position:absolute;left:0;width:260px;top:230px;font-size:24px;font-weight:500}
.member p{position:absolute;left:0;width:260px;top:276px;font-size:15px;line-height:26px;color:var(--muted)}
.orb{position:absolute;border-radius:50%}

/* footer */
.site-footer{left:0;top:3441px;width:1200px;height:348px;background:var(--black)}
.foot-brand,.foot-col,.copyright{color:var(--white)}
.foot-brand{left:115px;top:3568px;font-family:"Roboto",sans-serif;font-weight:500;font-size:50px;letter-spacing:2px}
.foot-col h4{font-size:18px;font-weight:500;text-transform:uppercase}
.foot-links{list-style:none;margin-top:24px;font-size:15px;line-height:22px}
.contact-row{display:flex;gap:14px;font-size:15px;line-height:25px;margin-top:14px}
.email-box{left:854px;top:3571px;width:234px;height:47px;background:var(--white);color:#777;font-size:15px;padding:14px 16px}
.submit{left:854px;top:3627px;width:122px;height:45px;background:var(--green);border-radius:0}
.copyright{left:0;width:1200px;top:3738px;text-align:center;font-size:15px}
</style>
</head>
<body>

<!-- hero -->
<div class="abs hero-photo" role="img" aria-label="Woman on a sofa smiling at her dog in a bright living room"></div>
<header class="abs site-header">
  <div class="brand">VETRIXO</div>
  <nav class="nav">
    <span class="active">HOME</span><span>MISSION</span><span>ANIMAL HEALTH</span><span>PARTNER</span><span>TEAM</span>
  </nav>
  <svg class="search" width="20" height="20" viewBox="0 0 20 20"><circle cx="8" cy="8" r="6" fill="none" stroke="#8fb31d" stroke-width="3"/><path d="M12.5 12.5 18 18" stroke="#8fb31d" stroke-width="3" stroke-linecap="round"/></svg>
  <a class="btn login">LOG IN</a>
</header>

<svg class="abs hero-blob" viewBox="0 0 450 450">
  <defs><linearGradient id="blobGrad" x1="0" y1="1" x2="1" y2="0"><stop offset="0" stop-color="#4f87b8"/><stop offset="1" stop-color="#2e2d4d"/></linearGradient></defs>
  <path d="M205 5C265-12 345 40 400 110C450 170 455 240 430 300C400 375 320 440 200 448C110 452 15 410 3 320C-8 250 10 160 60 125C110 90 150 20 205 5Z" fill="url(#blobGrad)"/>
</svg>
<div class="abs hero-copy">
  <div class="hero-kicker">WELCOME TO</div>
  <h1 class="hero-name">VETRIXO</h1>
  <div class="hero-sub">Vetrixo is deploying a Software as a Service</div>
</div>
<a class="btn hero-btn">GET STARTED</a>
<div class="abs dots"><span></span><span class="on"></span><span></span></div>

<!-- mission -->
<section class="abs mission" role="img" aria-label="Faded photo of a pet owner with a dog"></section>
<h2 class="section-title" style="top:766px">OUR MISSION</h2>
<div class="title-bar" style="left:578px;top:804px"></div>
<p class="abs mission-text">Vetrixo is deploying a Software as a Service (SaaS) platform to facilitate the efficient collection, transmission, secure storage and anonymised analysis of data integral to animal diagnostics.</p>
<a class="btn mission-btn">LEARN MORE</a>

<!-- capabilities -->
<h2 class="abs cap-title">CAPABILITIES</h2>
<div class="title-bar" style="left:112px;top:1216px"></div>
<ul class="abs cap-list">
  <li><svg class="tick" viewBox="0 0 20 20"><circle cx="10" cy="10" r="8" fill="none" stroke="#8fb31d" stroke-width="1.6"/><path d="M6 10l3 3 6-7" fill="none" stroke="#8fb31d" stroke-width="1.8"/></svg><span>Originally developed for the human market, the core platform has been deployed in the UK and Ireland and has been used to securely process nearly 3 million cases</span></li>
  <li><svg class="tick" viewBox="0 0 20 20"><circle cx="10" cy="10" r="8" fill="none" stroke="#8fb31d" stroke-width="1.6"/><path d="M6 10l3 3 6-7" fill="none" stroke="#8fb31d" stroke-width="1.8"/></svg><span>The platform has been widely used by leading pharmacies, employers, the national health service and most of the UK’s largest private sector laboratories</span></li>
</ul>
<a class="btn cap-btn">LEARN MORE</a>
<div class="abs cap-frame"></div>
<div class="abs cap-photo" role="img" aria-label="Woman hugging a long-haired tabby cat"></div>

<!-- turnkey -->
<section class="abs turnkey"></section>
<div class="abs turnkey-photo" role="img" aria-label="Family on a sofa with a golden retriever in the foreground"></div>
<div class="abs turnkey-copy">
  <h2>Turnkey initial veterinary deployment<br>– Animal health and welfare pathway</h2>
  <p>Vetrixo is finalising the design of a bespoke platform to facilitate the collection and processing of data and tests for the Animal Health and Welfare Pathway. Key elements include:</p>
  <ul>
    <li><svg class="tick" viewBox="0 0 20 20"><circle cx="10" cy="10" r="8" fill="none" stroke="#fff" stroke-width="1.6"/><path d="M6 10l3 3 6-7" fill="none" stroke="#fff" stroke-width="1.8"/></svg>Facilitated data collection at the farm by vets</li>
    <li><svg class="tick" viewBox="0 0 20 20"><circle cx="10" cy="10" r="8" fill="none" stroke="#fff" stroke-width="1.6"/><path d="M6 10l3 3 6-7" fill="none" stroke="#fff" stroke-width="1.8"/></svg>Secure and efficient processing of test samples by labs</li>
    <li><svg class="tick" viewBox="0 0 20 20"><circle cx="10" cy="10" r="8" fill="none" stroke="#fff" stroke-width="1.6"/><path d="M6 10l3 3 6-7" fill="none" stroke="#fff" stroke-width="1.8"/></svg>Digital results reporting</li>
    <li><svg class="tick" viewBox="0 0 20 20"><circle cx="10" cy="10" r="8" fill="none" stroke="#fff" stroke-width="1.6"/><path d="M6 10l3 3 6-7" fill="none" stroke="#fff" stroke-width="1.8"/></svg>Invoice support</li>
    <li><svg class="tick" viewBox="0 0 20 20"><circle cx="10" cy="10" r="8" fill="none" stroke="#fff" stroke-width="1.6"/><path d="M6 10l3 3 6-7" fill="none" stroke="#fff" stroke-width="1.8"/></svg>Data analysis reporting</li>
  </ul>
</div>
<a class="btn btn-outline turnkey-btn">LEARN MORE</a>

<!-- joint venture -->
<h2 class="section-title" style="top:2256px;font-size:27px;font-weight:500">VETRIXO IS A JOINT VENTURE BETWEEN</h2>
<div class="title-bar" style="left:578px;top:2294px"></div>
<article class="abs jv-card jv-blue" role="img" aria-label="Blue-tinted photo of livestock research">
  <h3>Ridgeway Solutions Limited</h3>
  <p>An innovative veterinary-led, close to market sustainable food research organisation. Ridgeway brings together a team of highly experienced vets representing key opinion leaders within the livestock industry and additional technical support staff through its shareholder practice Hartfield Veterinary Group, Yorkshire.</p>
  <a class="btn btn-outline jv-btn">LEARN MORE</a>
</article>
<article class="abs jv-card jv-green" role="img" aria-label="Green-tinted photo of a laboratory">
  <h3>Tailored Diagnostics Limited</h3>
  <p>Is a rapidly growing Software as a Service platform provider in the digital health market. TDX deploys its agile and collaborativesoftware development process working in partnership with its clients, using the skillsof both parties to build the best solutions as effectively and efficiently as possible. Its</p>
  <a class="btn btn-outline jv-btn">LEARN MORE</a>
</article>

<!-- team -->
<section class="abs team" role="img" aria-label="Faded background photo of a cat"></section>
<h2 class="section-title" style="top:2900px">OUR TEAM</h2>
<div class="title-bar" style="left:578px;top:2938px"></div>

<div class="abs member" style="left:89px">
  <span class="orb" style="left:28px;top:10px;width:30px;height:30px;background:var(--navy)"></span>
  <div class="avatar-ring"></div>
  <div class="avatar" role="img" aria-label="Portrait of a team member" style="background:linear-gradient(160deg,#d8d8d8,#a9a39a)"></div>
  <span class="orb" style="left:147px;top:-12px;width:46px;height:46px;background:var(--blue)"></span>
  <h4>Owen Marsh</h4>
  <p>Lorem ipsum dolor sit amet, consectetur adipiscing elit, sed labore et dolore magna aliqua.</p>
</div>
<div class="abs member" style="left:344px">
  <span class="orb" style="left:60px;top:-18px;width:40px;height:40px;background:var(--green)"></span>
  <div class="avatar-ring" style="background:var(--green)"></div>
  <div class="avatar" role="img" aria-label="Portrait of a team member" style="background:linear-gradient(160deg,#d6d6d6,#9a8f86)"></div>
  <span class="orb" style="left:164px;top:0;width:32px;height:32px;background:var(--navy)"></span>
  <h4>Dana Holloway</h4>
  <p>Lorem ipsum dolor sit amet, consectetur adipiscing elit, sed labore et dolore magna aliqua.</p>
</div>
<div class="abs member" style="left:598px">
  <span class="orb" style="left:73px;top:-22px;width:28px;height:28px;background:var(--navy)"></span>
  <span class="orb" style="left:50px;top:0;width:18px;height:18px;background:var(--blue)"></span>
  <div class="avatar-ring"></div>
  <div class="avatar" role="img" aria-label="Portrait of a team member" style="background:linear-gradient(160deg,#e0e0e0,#7f858c)"></div>
  <span class="orb" style="left:143px;top:-10px;width:40px;height:40px;background:var(--green)"></span>
  <h4>Leo Brandt</h4>
  <p>Lorem ipsum dolor sit amet, consectetur adipiscing elit, sed labore et dolore magna aliqua.</p>
</div>
<div class="abs member" style="left:852px">
  <div class="avatar-ring"></div>
  <div class="avatar" role="img" aria-label="Portrait of a team member" style="background:linear-gradient(160deg,#cfe8ee,#b9d8e0)"></div>
  <span class="orb" style="left:152px;top:-12px;width:44px;height:44px;background:var(--blue)"></span>
  <h4>Mira Castell</h4>
  <p>Lorem ipsum dolor sit amet, consectetur adipiscing elit, sed labore et dolore magna aliqua.</p>
</div>

<!-- footer -->
<footer class="abs site-footer"></footer>
<div class="abs foot-brand">VETRIXO</div>
<div class="abs foot-col" style="left:394px;top:3524px">
  <h4>Quick Links</h4>
  <ul class="foot-links"><li>Home</li><li>Mission</li><li>Animal Health</li><li>Partner</li><li>Team</li></ul>
</div>
<div class="abs foot-col" style="left:565px;top:3524px;width:260px">
  <h4>Contact Us</h4>
  <div class="contact-row" style="margin-top:20px"><svg width="16" height="22" viewBox="0 0 16 22"><path d="M8 1a7 7 0 0 1 7 7c0 5-7 13-7 13S1 13 1 8a7 7 0 0 1 7-7z" fill="#fff"/><circle cx="8" cy="8" r="2.6" fill="#000"/></svg><span>Lorem ipsum dolor sit amet,<br>consectetur</span></div>
  <div class="contact-row"><svg width="16" height="18" viewBox="0 0 24 24"><path d="M6.6 10.8a15 15 0 0 0 6.6 6.6l2.2-2.2a1 1 0 0 1 1-.25 11.4 11.4 0 0 0 3.6.57 1 1 0 0 1 1 1V20a1 1 0 0 1-1 1A17 17 0 0 1 3 4a1 1 0 0 1 1-1h3.5a1 1 0 0 1 1 1c0 1.25.2 2.45.57 3.57a1 1 0 0 1-.25 1z" fill="#fff"/></svg><span>+1 (555) 010 0100</span></div>
  <div class="contact-row"><svg width="16" height="18" viewBox="0 0 16 16"><rect x="0" y="3" width="16" height="11" fill="#fff"/><path d="M0 3l8 6 8-6" fill="none" stroke="#000" stroke-width="1.4"/></svg><span>info@vetrixo.example</span></div>
</div>
<div class="abs foot-col" style="left:854px;top:3524px"><h4>Sing up for newsletter</h4></div>
<div class="abs email-box">Email Address</div>
<a class="btn submit">SUBMIT</a>
<div class="abs copyright">©Copyrights 2022 Vetrixo &nbsp;| &nbsp; All Rights Reserved</div>

</body>
</html>
```